Corporate Business Card

Very professional, Modern, Not to busy, include phone address email, website
(253) 617-4930, 18761 52nd Avenue S, Kent, WA 98047, martin@plumlinegroup.com, varkoworks.com

Target Market(s)

Manufacturing

Industry/Entity Type

Aero, machining, manufacturing, Off road racing

Contact Information for Business Card

Phone, address email, website

```html
<!DOCTYPE html>
<html lang="en">
<head>
<meta charset="utf-8">
<title>Varko Works – Business Card</title>
<link rel="stylesheet" href="https://fonts.googleapis.com/css2?family=Poppins:wght@500;600;700&family=Arimo:wght@400&display=swap">
<style>
  :root {
    --navy: #163468;
    --board-blue: #1c4487;
    --board-grey: #efefef;
    --red: #d3232a;
    --band-red: #e60012;
    --white: #ffffff;
  }
  * { margin: 0; padding: 0; box-sizing: border-box; }
  html, body { width: 1075px; height: 1200px; overflow: hidden; }
  body {
    position: relative;
    background: var(--board-grey);
    font-family: "Arimo", Arial, sans-serif;
  }
  .board-top {
    position: absolute; left: 0; top: 0;
    width: 1075px; height: 461px;
    background: var(--board-blue);
  }
  .card {
    position: absolute; left: 206px;
    width: 663px; height: 396px;
    box-shadow: 3px 3px 2px rgba(0,0,0,0.55);
    overflow: hidden;
  }
  .card--front { top: 187px; background: var(--white); }
  .card--back { top: 637px; background: var(--navy); }

  .wordmark {
    position: absolute;
    font-family: "Poppins", Arial, sans-serif;
    font-weight: 700;
    letter-spacing: 1px;
    white-space: nowrap;
  }
  .card--front .wordmark {
    right: 40px; top: 72px;
    font-size: 54px; color: var(--navy);
  }
  .card--back .wordmark {
    left: 0; right: 0; top: 148px;
    text-align: center;
    font-size: 60px; color: var(--white);
  }

  .holder { position: absolute; left: 36px; top: 218px; }
  .holder__name {
    font-family: "Poppins", Arial, sans-serif;
    font-weight: 600; font-size: 23px; line-height: 1.1;
    color: var(--navy);
  }
  .holder__title {
    font-size: 17px; color: var(--red); line-height: 1.1; margin-top: 1px;
  }
  .holder__rule {
    width: 210px; height: 5px; background: var(--red); margin-top: 9px;
  }

  .info-band {
    position: absolute; left: 0; bottom: 0;
    width: 100%; height: 117px;
    background: var(--navy);
    color: var(--white);
  }
  .contacts { position: absolute; left: 36px; top: 20px; list-style: none; }
  .contacts li {
    display: flex; align-items: center; gap: 6px;
    font-size: 18px; line-height: 23.5px;
  }
  .contacts svg { width: 17px; height: 17px; flex: none; }
  .address {
    position: absolute; right: 41px; top: 48px;
    text-align: right; font-style: normal;
    font-size: 18px; line-height: 24px;
  }

  .web-band {
    position: absolute; left: 0; bottom: 0;
    width: 100%; height: 46px;
    background: var(--band-red);
    color: var(--white);
    font-size: 18px;
    display: flex; align-items: center; justify-content: center;
  }
</style>
</head>
<body>
  <div class="board-top"></div>

  <section class="card card--front">
    <div class="wordmark">VARKO WORKS</div>

    <div class="holder">
      <div class="holder__name">DANIEL HALE</div>
      <div class="holder__title">MANAGING DIRECTOR</div>
      <div class="holder__rule"></div>
    </div>

    <div class="info-band">
      <ul class="contacts">
        <li>
          <svg viewBox="0 0 24 24" aria-hidden="true"><path fill="#d3232a" d="M6.6 10.8a15.1 15.1 0 0 0 6.6 6.6l2.2-2.2c.3-.3.7-.4 1-.2 1.1.4 2.3.6 3.6.6.6 0 1 .4 1 1V20c0 .6-.4 1-1 1A17 17 0 0 1 3 4c0-.6.4-1 1-1h3.5c.6 0 1 .4 1 1 0 1.3.2 2.5.6 3.6.1.3 0 .7-.2 1z"/></svg>
          (253) 617-4930
        </li>
        <li>
          <svg viewBox="0 0 24 24" aria-hidden="true"><path fill="#d3232a" d="M2 5h20v14H2z"/><path fill="none" stroke="#163468" stroke-width="1.6" d="M2 5l10 8 10-8"/></svg>
          martin@plumlinegroup.com
        </li>
        <li>
          <svg viewBox="0 0 24 24" aria-hidden="true"><g fill="none" stroke="#d3232a" stroke-width="2"><circle cx="12" cy="12" r="9"/><ellipse cx="12" cy="12" rx="4" ry="9"/><path d="M3 12h18M5 7h14M5 17h14"/></g></svg>
          www.varkoworks.com
        </li>
      </ul>
      <address class="address">
        18761 52nd Avenue S<br>
        Kent, WA 98047
      </address>
    </div>
  </section>

  <section class="card card--back">
    <div class="wordmark">VARKO WORKS</div>
    <div class="web-band">www.varkoworks.com</div>
  </section>
</body>
</html>
```